Business Card Design for Brightlane

The company provides engineering tender consulting services and personnel resources. The target market is large engineering construction and services companies. The business is based in Australia.

```html
<!DOCTYPE html>
<html lang="en">
<head>
<meta charset="utf-8">
<title>Brightlane Business Card</title>
<link rel="stylesheet" href="https://fonts.googleapis.com/css2?family=Source+Sans+3:wght@300;400;600&display=swap">
<style>
  :root {
    --page-bg: #ececec;
    --card-bg: #ffffff;
    --brand-blue: #1a76bc;
    --brand-green: #a7c83a;
    --ink: #2b2b2b;
    --ink-soft: #555555;
    --ink-muted: #8a8a8a;
    --grey-dark: #c3c3c3;
    --grey-light: #dcdcdc;
  }
  * { box-sizing: border-box; margin: 0; padding: 0; }
  html, body {
    width: 1200px; height: 800px; overflow: hidden;
    background: var(--page-bg);
    font-family: "Source Sans 3", sans-serif;
  }
  .card {
    position: absolute;
    left: 279px;
    width: 634px;
    height: 363px;
    background: var(--card-bg);
    overflow: hidden;
  }
  .card--front { top: 16px; }
  .card--back { top: 424px; }

  .brand {
    position: absolute;
    left: 0; right: 0;
    display: flex; flex-direction: column; align-items: center;
  }
  .card--front .brand { top: 42px; }
  .card--back .brand { top: 40px; }
  .brand__square {
    width: 70px; height: 70px;
    background: var(--brand-green);
  }
  .card--back .brand__square { width: 62px; height: 62px; }
  .brand__name {
    margin-top: 14px;
    font-weight: 600;
    font-size: 29px;
    letter-spacing: -0.3px;
    color: var(--brand-blue);
    line-height: 1;
  }
  .card--back .brand__name { font-size: 23px; margin-top: 12px; }

  .contact-person {
    position: absolute;
    left: 27px; top: 230px;
    color: var(--ink-soft);
  }
  .contact-person__name {
    font-size: 25px; font-weight: 400; color: var(--ink);
    line-height: 1; margin-bottom: 6px;
  }
  .contact-person__line { font-size: 14.5px; line-height: 17px; font-weight: 300; }
  .label { color: var(--brand-green); }

  .contact-web {
    position: absolute;
    right: 27px; top: 292px;
    text-align: right;
    font-size: 14.5px; line-height: 17px; font-weight: 300;
    color: var(--ink-soft);
  }

  .card-band {
    position: absolute; left: 0; bottom: 0;
    width: 634px; height: 22px; display: block;
  }

  .services {
    position: absolute;
    left: 104px; top: 175px;
    list-style: none;
  }
  .services__item {
    display: flex; align-items: center;
    font-size: 14.5px; line-height: 22px; font-weight: 300;
    color: var(--ink-muted);
  }
  .services__item::before {
    content: "";
    width: 9px; height: 9px; margin-right: 6px;
    background: var(--brand-blue);
  }
</style>
</head>
<body>
  <section class="card card--front">
    <div class="brand">
      <div class="brand__square"></div>
      <div class="brand__name">Brightlane</div>
    </div>

    <div class="contact-person">
      <div class="contact-person__name">YOUR NAME</div>
      <div class="contact-person__line">PO Box 99 Nnnnnnnnnn,</div>
      <div class="contact-person__line">Nnn, 9999</div>
      <div class="contact-person__line"><span class="label">M:</span> 9999 999 999</div>
      <div class="contact-person__line"><span class="label">T:</span> 99 9999 9999</div>
    </div>

    <div class="contact-web">
      <div><span class="label">E:</span> nnnn@nnn.com.au</div>
      <div>www.brightlane.com.au</div>
    </div>

    <svg class="card-band" viewBox="0 0 634 22" preserveAspectRatio="none">
      <polygon points="0,0 452,0 468,22 0,22" fill="var(--brand-blue)"/>
      <polygon points="456,0 634,0 634,22 472,22" fill="var(--brand-green)"/>
      <line x1="453" y1="0" x2="469" y2="22" stroke="#1d2a3a" stroke-width="3"/>
    </svg>
  </section>

  <section class="card card--back">
    <div class="brand">
      <div class="brand__square"></div>
      <div class="brand__name">Brightlane</div>
    </div>

    <ul class="services">
      <li class="services__item">The target market is large engineering construction and services</li>
      <li class="services__item">The target market is large engineering construction and services</li>
      <li class="services__item">The target market is large engineering construction and services</li>
      <li class="services__item">The target market is large engineering construction and services</li>
      <li class="services__item">The target market is large engineering construction and services</li>
    </ul>

    <svg class="card-band" viewBox="0 0 634 22" preserveAspectRatio="none">
      <polygon points="0,0 450,0 466,22 0,22" fill="var(--grey-dark)"/>
      <polygon points="454,0 634,0 634,22 470,22" fill="var(--grey-light)"/>
    </svg>
  </section>
</body>
</html>
```